A new presentation to our clients

we are a Real Estate agency, our website is www.lumibrasa.com and it’s time to have a new, fashion and remarcable Business Card. we want to differentiate ourselves from other companies so we want a business card that differentiates us. we want the business card to impact our customers. in the competitive market that we have today, we have to be different and it is this difference that we seek

Target Market(s)

Real Estate Clients

Contact Information for Business Card

We search a totaly diferent card from the usual

Font styles to use
Sans Serif

Colors
e34197

Requirements
Must have
• Logo, adress, phone contact, e-mail, photo, and our website
Nice to have
• We would like to see a modern business card
Should not have
• Houses or building draws

```html
<!DOCTYPE html>
<html lang="en">
<head>
<meta charset="utf-8">
<title>Lumi Brasa — Business Card</title>
<link rel="stylesheet" href="https://fonts.googleapis.com/css2?family=Montserrat:wght@600;700&family=Hind:wght@400&display=swap">
<style>
  :root {
    --brand-pink: #e6246b;
    --card-white: #ffffff;
    --ink-dark: #444444;
    --ink-soft: #5a5a5a;
    --backdrop: #2b2b2b;
  }
  html, body {
    margin: 0;
    padding: 0;
    width: 1200px;
    height: 791px;
    overflow: hidden;
    background: var(--backdrop);
  }
  .card {
    position: absolute;
    left: 158px;
    top: 142px;
    width: 882px;
    height: 503px;
    border-radius: 24px;
    overflow: hidden;
    background: var(--card-white);
    box-shadow: 0 6px 18px rgba(0,0,0,0.45);
  }
  .card__band {
    position: absolute;
    inset: 0;
    width: 100%;
    height: 100%;
  }
  .card__band path { fill: var(--brand-pink); }
  .brand-name {
    position: absolute;
    left: 480px;
    width: 340px;
    top: 218px;
    text-align: center;
    font-family: "Montserrat", sans-serif;
    font-weight: 600;
    font-size: 52px;
    line-height: 60px;
    color: var(--card-white);
    margin: 0;
    letter-spacing: 0.5px;
  }
  .contact {
    position: absolute;
    left: 62px;
    top: 120px;
  }
  .contact__row {
    position: absolute;
    left: 0;
    display: flex;
    align-items: center;
    white-space: nowrap;
  }
  .contact__icon {
    width: 22px;
    height: 22px;
    margin-right: 15px;
    fill: var(--brand-pink);
  }
  .person-name {
    font-family: "Montserrat", sans-serif;
    font-weight: 700;
    font-size: 28px;
    color: var(--ink-dark);
    line-height: 32px;
    margin: 0;
  }
  .person-role {
    position: absolute;
    left: 37px;
    top: 34px;
    font-family: "Montserrat", sans-serif;
    font-weight: 600;
    font-size: 19px;
    color: var(--ink-dark);
    margin: 0;
    white-space: nowrap;
  }
  .contact__text {
    font-family: "Hind", sans-serif;
    font-size: 19px;
    line-height: 24px;
    color: var(--ink-soft);
  }
  .address-lines { display: block; }
</style>
</head>
<body>
  <main class="card">
    <svg class="card__band" viewBox="0 0 882 503" preserveAspectRatio="none" aria-hidden="true">
      <path d="M300 0 H882 V503 H575 C488 503 427 465 427 375 V155 C427 55 375 0 300 0 Z"/>
    </svg>

    <section class="contact">
      <div class="contact__row" style="top:0">
        <svg class="contact__icon" viewBox="0 0 24 24"><circle cx="12" cy="7" r="5"/><path d="M2 23 C2 15 22 15 22 23 Z"/></svg>
        <h1 class="person-name">MARTA REIS</h1>
      </div>
      <p class="person-role">CEO/FOUNDER</p>

      <div class="contact__row" style="top:77px; align-items:flex-start">
        <svg class="contact__icon" viewBox="0 0 24 24" style="margin-top:6px"><path d="M12 1 C6.5 1 3 5 3 9.5 C3 15 12 23 12 23 C12 23 21 15 21 9.5 C21 5 17.5 1 12 1 Z M12 13 A3.5 3.5 0 1 1 12 6 A3.5 3.5 0 1 1 12 13 Z" fill-rule="evenodd"/></svg>
        <span class="contact__text address-lines">Rua das Camélias, 118<br>4410-552, Vale do Sorriso</span>
      </div>

      <div class="contact__row" style="top:147px">
        <svg class="contact__icon" viewBox="0 0 24 24"><path d="M6.6 10.8 C8 13.6 10.4 16 13.2 17.4 L15.4 15.2 C15.7 14.9 16.1 14.8 16.4 15 C17.5 15.4 18.7 15.6 20 15.6 C20.6 15.6 21 16 21 16.6 V20 C21 20.6 20.6 21 20 21 C10.6 21 3 13.4 3 4 C3 3.4 3.4 3 4 3 H7.5 C8.1 3 8.5 3.4 8.5 4 C8.5 5.3 8.7 6.5 9.1 7.6 C9.2 7.9 9.1 8.3 8.9 8.6 Z"/></svg>
        <span class="contact__text">(+351) 220 555 140</span>
      </div>

      <div class="contact__row" style="top:172px">
        <svg class="contact__icon" viewBox="0 0 24 24"><rect x="6" y="2" width="12" height="6"/><path d="M2 9 H22 V18 H18 V14 H6 V18 H2 Z"/><rect x="7" y="15" width="10" height="7"/></svg>
        <span class="contact__text">(+351) 220 555 149</span>
      </div>

      <div class="contact__row" style="top:197px">
        <svg class="contact__icon" viewBox="0 0 24 24"><path d="M2 5 H22 V19 H2 Z M4 7 V8 L12 13 L20 8 V7 L12 12 Z" fill-rule="evenodd"/></svg>
        <span class="contact__text">geral@lumibrasa.com</span>
      </div>

      <div class="contact__row" style="top:222px">
        <svg class="contact__icon" viewBox="0 0 24 24"><path d="M12 2 A10 10 0 1 0 12 22 A10 10 0 1 0 12 2 Z M7 6 C9 7 8 9 10 10 C12 11 11 13 13 14 C14 15 12 18 11 20 C7 19 4 16 4 12 C4 9.5 5 7.5 7 6 Z M15 4.5 C18 6 20 9 20 12 C18 12 17 10 15.5 9 C14 8 15 6 15 4.5 Z" fill-rule="evenodd"/></svg>
        <span class="contact__text">www.lumibrasa.com</span>
      </div>
    </section>

    <p class="brand-name">Lumi Brasa</p>
  </main>
</body>
</html>
```